Flyer, poster, banner and social media titles designs for Community Mending Chartre

The Harbourline Charter for Community Mending provide a nationally agreed framework to guide recovery policy and practice across Australia. The Principles support recovery practitioners, governments, non-government organisations and communities to deliver effective, community-centred recovery outcomes.
The Principles have recently been refreshed through extensive consultation and we require a contemporary visual identity and design suite that will increase awareness, engagement and practical application of the Principles.
The redesign will cover:
• A4 Brochure (primary publication)
• A3 Poster
• Pull up banner
• Social Media Tiles
The new design should:
• Create a recognisable brand for the Harbourline Charter.
• Appeal to both experienced and emerging recovery practitioners.
• Reflect contemporary disaster recovery practice.
• Feel people-focused rather than government-focused.
• Support future resources such as videos, implementation guides, presentations and workshop materials.
• Remain relevant for several years without requiring a major redesign.
Target Audience
• Disaster recovery practitioners
• Government agencies
• Non-government organisations
• Community recovery workers
• Recovery managers and leaders
• Community stakeholders and volunteers
The visual identity should reflect the six Principles:
• Understanding Context
• Recognising Complexity
• Community-Centred Approaches
• Coordination
• Communication
• Capacity Building
The design should communicate:
• Recovery is centred on people and communities.
• Recovery is collaborative and involves many sectors.
• Recovery is adaptive, inclusive and evidence-informed.
• Recovery supports resilience and long-term wellbeing.
• The Principles provide practical guidance for recovery practice.
We are looking for:
• Modern and professional
• Warm and approachable
• Human-centred
• Inclusive and accessible
• Australian in context
• Visually engaging
• Suitable for print and digital use
We would like to avoid:
• Images of disaster destruction
• Emergency response imagery (fire trucks, flashing lights, etc.)
• Overly corporate or bureaucratic designs
• Designs that focus on deficits rather than recovery and growth
Consider themes such as:
• Connection and collaboration
• Communities and people
• Growth, recovery and renewal
Accessibility
Designs should:
• Meet accessibility best practice
• Use clear typography
• Achieve strong colour contrast
• Be suitable for both digital and print formats

Deliverables
1. Principles Brochure
• A4 trifold size x 2 (online and print friendly version)
• A side to include cover side, logos side and overview of principles.
• B side full details of the principles
• Graphic to highlight the 3 c’s concept (RECOVERY Context, complexity, community centred, coordinate, communicate and capacity). Currently 3 circles.
• Can be printed and distributed electronically
2. Poster
• A1 and A3 versions
• Suitable for office and workshop display
3. Pull-Up Banner - 850 mm (W) × 2000 mm (H)
• Conference and event use
• High visual impact
• Strong branding and concise messaging
4. Social Media Tiles x 3

We are providing an extension and increasing the budget following feedback from designers. We are wanting the resources to look and feel different from the existing designs, considering either a different colour palette in the designs or different motif with the leave design. Any nature based designs should consider the Australian fauna or flora. Also suggest avoiding images in the designs. The principles are not numbered or liner in the concept of how they function. Happy to answer any further questions and thank you for your suggested concepts.

Disaster recovery practitioners, Government agencies , Non-government organisations, Community recovery workers and Community stakeholders and volunteers

Disaster recovery

• Modern, warm, visually engaging, human-centred, Australian in context and different to the current design.
• Symbols for each principles
• Images of disaster destruction, Emergency response imagery, Overly corporate or bureaucratic designs, Designs that focus on deficits rather than recovery and growth, avoid too much black

```html
<!DOCTYPE html>
<html lang="en">
<head>
<meta charset="utf-8">
<title>Harbourline Charter for Community Mending – Identity Suite</title>
<link rel="stylesheet" href="https://fonts.googleapis.com/css2?family=Inter:wght@400;500&family=Source+Serif+4:wght@500;600&display=swap">
<style>
:root{
  --board:#ebe9e6;
  --cream:#f8f5ef;
  --sand:#ecdcc9;
  --tan:#d4a57c;
  --sage:#5f7d5e;
  --sage-light:#9cb598;
  --sky:#bad4ea;
  --slate:#3f4a5c;
  --ink:#1f2326;
  --serif:"Source Serif 4", Georgia, serif;
  --sans:"Inter", Arial, sans-serif;
}
*{box-sizing:border-box;margin:0;padding:0}
html,body{width:1200px;height:670px;overflow:hidden}
body{background:var(--board);position:relative;font-family:var(--sans);color:var(--ink)}
.label{position:absolute;font-size:13px;font-weight:400;color:var(--ink);white-space:nowrap}
.piece{position:absolute;background:var(--cream);box-shadow:0 1px 3px rgba(0,0,0,.12);overflow:hidden}
.title{font-family:var(--serif);font-weight:600;color:var(--ink);line-height:.98;position:absolute;z-index:1;white-space:nowrap}
.art{position:absolute;left:0;right:0;bottom:0}
.land{background:linear-gradient(180deg,var(--sky) 0%,var(--sand) 22%,var(--sage-light) 42%,var(--tan) 62%,var(--sage) 82%,var(--sky) 100%)}
.land-dark{background:linear-gradient(180deg,var(--tan) 0%,var(--sage-light) 30%,var(--slate) 60%,var(--sky) 80%,var(--sage) 100%)}
.brand{position:absolute;display:flex;align-items:center;gap:3px;font-family:var(--serif);font-weight:500;line-height:1.15}
.brand i{display:block;border-radius:50%;flex:none}

/* brochure */
.brochure{left:44px;top:57px;width:302px;height:210px;display:flex}
.brochure .panel{position:relative;width:33.333%;height:100%}
.panel-intro{padding:12px 10px}
.panel-intro h3{font-family:var(--serif);font-size:7px;font-weight:600;line-height:1.15;margin-bottom:8px}
.panel-intro p,.panel-intro li{font-size:3.4px;line-height:1.45;color:#333;margin-bottom:4px}
.panel-intro ul{padding-left:5px}
.panel-contact{background:var(--sage);color:#eef2ea}
.panel-contact .brand{left:12px;top:150px;color:#fff;font-size:4.2px;flex-direction:column;align-items:flex-start}
.panel-contact .brand i{width:14px;height:14px;border:1px solid #fff}
.panel-contact .contact{position:absolute;left:12px;top:175px;font-size:3.6px;line-height:1.5}
.panel-cover .brand{left:13px;top:14px;font-size:3.8px;color:var(--ink)}
.panel-cover .brand i{width:13px;height:13px;background:var(--slate)}

/* icons */
.roundel{position:absolute;width:88px;height:88px;border-radius:50%}
.roundel-cap{position:absolute;width:120px;text-align:center;font-size:14px;line-height:1.05}

/* relationship */
.relation{left:442px;top:396px;width:316px;height:226px}
.relation .head{position:absolute;left:23px;top:14px;font-size:8px;font-weight:500}
.relation .foot{position:absolute;left:0;right:0;top:200px;text-align:center;font-size:7px;font-weight:500}

/* typography card */
.type-card{left:800px;top:479px;width:121px;height:143px;display:flex;flex-direction:column}
.type-card .row{padding:0 8px;display:flex;align-items:center}
.swatches{display:flex;flex:1}
.swatches span{flex:1}
</style>
</head>
<body>

<!-- Brochure -->
<div class="label" style="left:44px;top:33px">A4 trifold brochure</div>
<div class="piece brochure">
  <div class="panel panel-intro">
    <h3>Harbourline Charter<br>for Community Mending</h3>
    <p>The Harbourline Charter for Community Mending guides how communities, agencies and partners work together on recovery across Australia.</p>
    <p>It draws on practice and lived experience to help people plan, act and reflect as they rebuild places, services and wellbeing over time.</p>
    <ul>
      <li>Recovery starts with local knowledge and respect for community priorities.</li>
      <li>Many sectors share the work and the decisions.</li>
      <li>Plans adapt as needs change over time.</li>
      <li>Clear, open information builds trust.</li>
      <li>Strong local capacity supports long-term recovery.</li>
    </ul>
  </div>
  <div class="panel panel-contact">
    <div class="brand"><i></i><span>Community Renewal Office</span></div>
    <div class="contact">Enquiries and feedback<br>hello@harbourlinecharter.org<br><br>Download the charter<br>www.harbourlinecharter.org</div>
  </div>
  <div class="panel panel-cover">
    <div class="brand"><i></i><span>Community Renewal Office</span></div>
    <div class="title" style="left:13px;top:50px;font-size:12.5px;font-weight:500">Harbourline<br>Charter for<br>Community<br>Mending</div>
    <div class="art land" style="height:90px" role="img" aria-label="Layered hills and winding river landscape"></div>
  </div>
</div>
<div class="label" style="left:44px;top:274px">Front trifold panel</div>

<!-- A1 poster -->
<div class="label" style="left:384px;top:33px">A1 poster</div>
<div class="piece" style="left:384px;top:57px;width:207px;height:293px">
  <div class="title" style="left:30px;top:58px;font-size:24px">Harbourline<br>Charter for<br>Community<br>Mending</div>
  <div class="art land" style="height:120px" role="img" aria-label="Layered hills with a river winding through green and ochre country"></div>
</div>
<div class="label" style="left:384px;top:357px">A1 poster</div>

<!-- A3 poster -->
<div class="piece" style="left:608px;top:57px;width:158px;height:229px">
  <div class="title" style="left:15px;top:43px;font-size:15px;font-weight:500">Harbourline<br>Charter for<br>Community<br>Mending</div>
  <div class="art land" style="height:115px" role="img" aria-label="River valley landscape with soft hills"></div>
</div>
<div class="label" style="left:608px;top:292px">A3 poster</div>

<!-- Banner -->
<div class="label" style="left:800px;top:33px">Conference pull-up banner</div>
<div class="piece" style="left:800px;top:57px;width:154px;height:371px;border-top:4px solid #c8c8c8;border-bottom:4px solid #c8c8c8">
  <div class="title" style="left:18px;top:42px;font-size:19px">Harbourline<br>Charter for<br>Community<br>Mending</div>
  <div class="art land" style="bottom:115px;height:115px" role="img" aria-label="Hills and river flowing forward toward an arrow"></div>
  <div style="position:absolute;left:0;right:0;top:248px;height:33px;background:var(--slate);color:#fff;font-size:10px;display:flex;align-items:center;justify-content:center">harbourlinecharter.org</div>
  <div style="position:absolute;left:0;right:0;top:281px;bottom:0;background:var(--sage)">
    <div class="brand" style="left:40px;top:20px;color:#fff;font-size:5px"><i style="width:12px;height:12px;border:1px solid #fff"></i><span>Community<br>Renewal Office</span></div>
  </div>
</div>

<!-- Social tiles top -->
<div class="label" style="left:993px;top:33px">Social media graphics</div>
<div class="piece" style="left:993px;top:57px;width:163px;height:163px">
  <div class="title" style="left:14px;top:26px;font-size:15.5px;font-weight:500">Harbourline<br>Charter for<br>Community<br>Mending</div>
  <div class="art land-dark" style="height:62px" role="img" aria-label="Dark hills and river landscape"></div>
</div>
<div class="piece" style="left:993px;top:230px;width:163px;height:100px">
  <div class="art" style="top:0;background:linear-gradient(90deg,var(--slate) 0%,var(--sage-light) 38%,var(--cream) 55%,var(--tan) 100%)" role="img" aria-label="River curve and native wildflowers"></div>
  <div class="brand" style="left:88px;top:10px;font-size:3.8px;color:var(--ink)"><i style="width:10px;height:10px;background:var(--slate)"></i><span>Community<br>Renewal Office</span></div>
</div>
<div class="label" style="left:993px;top:336px">Print-ready</div>

<!-- Social tiles bottom -->
<div class="label" style="left:993px;top:372px">Social media graphics</div>
<div class="piece" style="left:993px;top:398px;width:48px;height:105px;background:var(--sand)">
  <div style="height:40px;font-size:36px;line-height:40px;text-align:center;color:var(--slate)">Aa</div>
  <div style="height:40px;font-size:36px;line-height:40px;text-align:center;color:var(--sage-light);background:var(--cream)">Ar</div>
  <div style="height:25px;background:var(--slate)" role="img" aria-label="Textured grass pattern"></div>
</div>
<div class="piece" style="left:1052px;top:399px;width:104px;height:104px">
  <div class="title" style="left:8px;top:14px;font-size:9px;font-weight:500">Harbourline<br>Charter for<br>Community<br>Mending</div>
  <div class="art" style="top:0;left:68px;background:linear-gradient(180deg,var(--sage),var(--sky) 60%,var(--sage))" role="img" aria-label="Winding river beside green hills"></div>
  <div class="art" style="height:24px;right:36px;background:var(--tan)" role="img" aria-label="Ochre contour hill"></div>
</div>
<div class="piece" style="left:934px;top:518px;width:104px;height:104px">
  <div class="title" style="left:9px;top:12px;font-size:10px;font-weight:500">Harbourline<br>Charter for<br>Community<br>Mending</div>
  <div class="art land-dark" style="height:38px" role="img" aria-label="Dark hills and river landscape"></div>
</div>
<div class="piece" style="left:1052px;top:518px;width:104px;height:104px">
  <div class="title" style="left:9px;top:12px;font-size:10px;font-weight:500">Harbourline<br>Charter for<br>Community<br>Mending</div>
  <div class="art" style="height:40px;background:linear-gradient(90deg,var(--slate),var(--sand) 40%,var(--tan) 70%,var(--sage))" role="img" aria-label="Hills with native wildflowers"></div>
</div>

<!-- Typography -->
<div class="label" style="left:800px;top:457px">Typography</div>
<div class="piece type-card">
  <div class="row" style="height:38px;background:var(--sand);font-size:30px;color:var(--slate)">AaG<span style="color:var(--sage)">Op</span></div>
  <div class="row" style="height:26px;font-size:15px">Inter Sans</div>
  <div class="row" style="height:26px;background:var(--sand);font-size:7px;line-height:1.3">Geometric<br>Sans typeface</div>
  <div class="row" style="height:26px;font-size:14px">Color</div>
  <div class="swatches">
    <span style="background:var(--slate)"></span><span style="background:var(--sage)"></span><span style="background:var(--sage-light)"></span><span style="background:var(--tan)"></span><span style="background:var(--sand)"></span>
  </div>
</div>
<div class="label" style="left:800px;top:629px">Print-ready</div>

<!-- Icons -->
<div class="label" style="left:44px;top:339px">Icons</div>
<div class="roundel" style="left:56px;top:371px;background:linear-gradient(180deg,var(--sage-light),var(--tan) 55%,var(--slate))" role="img" aria-label="Context icon: layered land with compass"></div>
<div class="roundel" style="left:176px;top:369px;background:linear-gradient(135deg,var(--sage) 20%,var(--sky) 50%,var(--tan) 80%)" role="img" aria-label="Complexity icon: braided river through country"></div>
<svg class="roundel" style="left:296px;top:369px" viewBox="0 0 88 88" aria-label="Community-centred icon: three linked rings" role="img">
  <circle cx="32" cy="52" r="25" fill="none" stroke="var(--sage-light)" stroke-width="5"/>
  <circle cx="56" cy="52" r="25" fill="none" stroke="var(--tan)" stroke-width="5"/>
  <circle cx="44" cy="32" r="25" fill="none" stroke="var(--slate)" stroke-width="5"/>
</svg>
<div class="roundel-cap" style="left:40px;top:462px">Context</div>
<div class="roundel-cap" style="left:160px;top:462px">Complexity</div>
<div class="roundel-cap" style="left:280px;top:462px">Community-<br>centred</div>

<svg class="roundel" style="left:56px;top:501px" viewBox="0 0 88 88" role="img" aria-label="Coordination icon: crossing paths with arrows">
  <circle cx="44" cy="44" r="44" fill="var(--sage)"/>
  <path d="M0 44H88" stroke="var(--tan)" stroke-width="8"/>
  <path d="M44 0V88" stroke="var(--slate)" stroke-width="8"/>
  <path d="M52 44h20m-7-7 7 7-7 7" stroke="#fff" stroke-width="3" fill="none"/>
</svg>
<svg class="roundel" style="left:176px;top:501px" viewBox="0 0 88 88" role="img" aria-label="Communication icon: group with radiating arcs">
  <path d="M16 14a40 40 0 0 0 0 60M72 14a40 40 0 0 1 0 60" stroke="var(--slate)" stroke-width="5" fill="none" stroke-linecap="round"/>
  <path d="M27 24a28 28 0 0 0 0 40M61 24a28 28 0 0 1 0 40" stroke="var(--sage-light)" stroke-width="5" fill="none" stroke-linecap="round"/>
  <path d="M36 33a16 16 0 0 0 0 22M52 33a16 16 0 0 1 0 22" stroke="var(--tan)" stroke-width="5" fill="none" stroke-linecap="round"/>
  <circle cx="44" cy="40" r="4" fill="var(--sage)"/><rect x="37" y="46" width="14" height="9" rx="4" fill="var(--sage)"/>
</svg>
<div class="roundel" style="left:296px;top:501px;background:radial-gradient(circle at 60% 40%,var(--tan),var(--sage-light) 55%,var(--sage))" role="img" aria-label="Capacity icon: native wildflowers growing with upward arrow"></div>
<div class="roundel-cap" style="left:40px;top:592px">Coordination</div>
<div class="roundel-cap" style="left:160px;top:592px">Communication</div>
<div class="roundel-cap" style="left:280px;top:592px">Capacity</div>
<div class="label" style="left:44px;top:629px">Roundels</div>

<!-- Relationship diagram -->
<div class="piece relation">
  <div class="head">Context ⇒ Complexity</div>
  <div style="position:absolute;left:24px;top:42px;width:165px;height:145px;background:linear-gradient(180deg,var(--sage-light),var(--tan) 45%,var(--sage) 70%,var(--slate));clip-path:polygon(0 30%,45% 0,100% 25%,100% 70%,55% 100%,0 72%)" role="img" aria-label="Layered landscape block with a river"></div>
  <svg style="position:absolute;left:138px;top:34px" width="156" height="156" viewBox="0 0 156 156">
    <circle cx="78" cy="78" r="77" fill="var(--sky)"/>
    <circle cx="78" cy="78" r="63" fill="var(--sage-light)"/>
    <circle cx="78" cy="78" r="48" fill="var(--sage)"/>
    <circle cx="78" cy="78" r="34" fill="var(--slate)"/>
    <circle cx="78" cy="78" r="18" fill="var(--sand)"/>
    <text x="78" y="40" font-family="Inter, sans-serif" font-size="7" fill="#fff" text-anchor="middle">Coordination</text>
    <text x="78" y="25" font-family="Inter, sans-serif" font-size="6.5" fill="#fff" text-anchor="middle">Concentric ecosystem</text>
    <text x="78" y="124" font-family="Inter, sans-serif" font-size="7" fill="#fff" text-anchor="middle">Complexity</text>
    <text x="82" y="140" font-family="Inter, sans-serif" font-size="7" fill="#fff" text-anchor="middle">Equally important</text>
  </svg>
  <div class="foot">Context / Complexity</div>
</div>
<div class="label" style="left:442px;top:629px">New relationship</div>

</body>
</html>
```